We are a local Communty Pharmacy wishing to promote and market a specialised Pharmaceutical Service

We would like a design that is professional and enticing ( according to the brief In attached files)
We wish to Market Compounding Pharmacy as a specialist side of our business.
We have the expertise a purpose built preparation laboratory.
The main purpose is an Internet presence that entices prospective patients to contact or visit our physical store.

Target Market(s)

Patients Medicos and Veterinary clients

Industry/Entity Type

Pharmacy

Coding

Coded - Design and coding required

Number of Pages Required

1 page

Requirements
Must have
• Clear friendly image
Nice to have
• soft enticing feel
Should not have
• No crass loud unprofessional elements

```html
<!DOCTYPE html>
<html lang="en">
<head>
<meta charset="utf-8">
<title>Westbrook Compounding Pharmacy</title>
<link href="https://fonts.googleapis.com/css2?family=Open+Sans:wght@400;600;700&family=Roboto:wght@400;500;700&display=swap" rel="stylesheet">
<style>
:root{
  --blue:#1b5fae;
  --blue-dark:#0e3f7e;
  --blue-deep:#0a2f5f;
  --blue-light:#2f7fd0;
  --green:#6cbf3a;
  --text:#555b63;
  --heading:#2b3440;
  --page:#eef2f6;
  --white:#ffffff;
}
*{box-sizing:border-box;margin:0;padding:0}
html,body{width:1200px;height:2264px;overflow:hidden}
body{background:var(--page);font-family:"Open Sans",sans-serif;color:var(--text);position:relative}
.site-header{position:absolute;left:0;top:0;width:1200px;height:216px;background:linear-gradient(180deg,#2a6fc0,var(--blue))}
.brand{position:absolute;left:140px;top:40px;width:420px;display:flex;align-items:center;gap:14px}
.brand-mark{width:56px;height:56px;border-radius:50%;background:var(--white);flex:none}
.brand-name{font-family:"Roboto",sans-serif;font-weight:700;font-size:26px;color:var(--white);line-height:1.15}
.header-contact{position:absolute;right:140px;top:16px;width:420px;color:var(--white);font-size:13px}
.header-contact h2{font-family:"Roboto",sans-serif;font-size:18px;font-weight:700;text-align:right;margin-bottom:14px;letter-spacing:.5px}
.hc-row{display:flex;justify-content:space-between;margin-bottom:8px}
.hc-item{display:flex;align-items:center;gap:6px}
.hc-item svg{width:14px;height:14px;fill:var(--white)}
.main-nav{position:absolute;left:140px;top:168px;width:920px;height:44px;background:var(--blue-dark);display:flex}
.main-nav a{color:var(--white);text-decoration:none;font-family:"Roboto",sans-serif;font-size:15px;padding:0 22px;line-height:44px}
.main-nav a.active{background:var(--blue-light)}
.hero{position:absolute;left:140px;top:216px;width:920px;height:544px}
.hero-photo{position:absolute;inset:0;background:linear-gradient(110deg,#eaf3fb 0%,#9fc6e8 45%,#3f86c8 100%)}
.hero-copy{position:absolute;right:40px;top:150px;width:470px;text-align:center;color:var(--white)}
.hero-copy h1{font-family:"Roboto",sans-serif;font-size:34px;font-weight:700;letter-spacing:1px;white-space:nowrap}
.hero-copy h3{font-size:22px;font-weight:600;color:#d7f0bf;margin:6px 0 16px}
.hero-copy p{font-size:13px;line-height:1.6}
.hero-btn{display:inline-block;margin-top:26px;border:1px solid var(--white);color:var(--white);padding:10px 26px;font-size:13px}
.content{position:absolute;left:140px;top:760px;width:920px;height:1100px;background:var(--white);padding:40px 40px 0;text-align:center}
.content h2{font-family:"Roboto",sans-serif;font-size:28px;font-weight:700;color:var(--heading)}
.subtitle{color:var(--green);font-size:17px;margin:8px 0 30px}
.content p.body{font-size:13px;line-height:1.75;text-align:left}
.services{display:flex;justify-content:space-between;margin:36px 30px 40px}
.service{width:180px}
.service-icon{width:116px;height:116px;border-radius:50%;background:var(--blue);margin:0 auto 18px;display:flex;align-items:center;justify-content:center}
.service-icon.green{background:var(--green)}
.service-icon svg{width:56px;height:56px}
.service h4{font-family:"Roboto",sans-serif;font-size:14px;font-weight:700;color:var(--heading);margin-bottom:8px}
.service p{font-size:11px;line-height:1.5}
.features-title{margin-top:50px}
.features{display:flex;justify-content:space-between;margin-top:34px}
.feature{width:264px;text-align:left}
.feature-photo{height:180px}
.feature h5{font-size:13px;font-weight:700;color:var(--heading);margin-top:14px;text-transform:uppercase}
.site-footer{position:absolute;left:0;top:1860px;width:1200px;height:360px;background:var(--blue);color:var(--white);display:flex;gap:60px;padding:40px 140px 0}
.footer-col{width:260px}
.footer-col h4{font-family:"Roboto",sans-serif;font-size:17px;font-weight:700;margin-bottom:18px}
.footer-col p{font-size:13px;line-height:1.7}
.map{width:280px;height:190px;background:linear-gradient(135deg,#dcd7b8,#c9c39e)}
.fc-item{display:flex;align-items:center;gap:10px;font-size:13px;margin-bottom:14px}
.fc-item svg{width:16px;height:16px;fill:var(--white)}
.copyright{position:absolute;left:0;top:2220px;width:1200px;height:44px;background:var(--blue-deep);color:#cfe0f3;font-size:12px;line-height:44px;padding-left:140px}
</style>
</head>
<body>
<header class="site-header">
  <div class="brand"><span class="brand-mark"></span><span class="brand-name">Westbrook<br>Compounding Pharmacy</span></div>
  <div class="header-contact">
    <h2>WESTBROOK COMPOUNDING PHARMACY</h2>
    <div class="hc-row">
      <span class="hc-item"><svg viewBox="0 0 24 24"><path d="M12 2a7 7 0 0 0-7 7c0 5 7 13 7 13s7-8 7-13a7 7 0 0 0-7-7zm0 9.5A2.5 2.5 0 1 1 12 6a2.5 2.5 0 0 1 0 5.5z"/></svg>Unit 3 / 12 Harbour Lane</span>
      <span class="hc-item"><svg viewBox="0 0 24 24"><path d="M6.6 10.8a15 15 0 0 0 6.6 6.6l2.2-2.2a1 1 0 0 1 1-.25 11.4 11.4 0 0 0 3.6.6 1 1 0 0 1 1 1V20a1 1 0 0 1-1 1A17 17 0 0 1 3 4a1 1 0 0 1 1-1h3.5a1 1 0 0 1 1 1c0 1.25.2 2.45.6 3.6a1 1 0 0 1-.25 1z"/></svg>08 5550 1234</span>
    </div>
    <div class="hc-row">
      <span class="hc-item" style="padding-left:20px">Westbrook WA 6000</span>
      <span class="hc-item"><svg viewBox="0 0 24 24"><path d="M6.6 10.8a15 15 0 0 0 6.6 6.6l2.2-2.2a1 1 0 0 1 1-.25 11.4 11.4 0 0 0 3.6.6 1 1 0 0 1 1 1V20a1 1 0 0 1-1 1A17 17 0 0 1 3 4a1 1 0 0 1 1-1h3.5a1 1 0 0 1 1 1c0 1.25.2 2.45.6 3.6a1 1 0 0 1-.25 1z"/></svg>08 5550 1235</span>
    </div>
    <div class="hc-row" style="justify-content:flex-end">
      <span class="hc-item"><svg viewBox="0 0 24 24"><path d="M2 5h20v14H2zm2 2v.5l8 5 8-5V7z"/></svg>compounding@westbrookchemist.example</span>
    </div>
  </div>
  <nav class="main-nav">
    <a class="active">Home</a><a>About us</a><a>Locations</a><a>Things</a><a>Contact</a>
  </nav>
</header>

<section class="hero">
  <div class="hero-photo" role="img" aria-label="Pharmacist in a laboratory preparing medication with a pipette and test tubes"></div>
  <div class="hero-copy">
    <h1>COMPOUNDING PHARMACY</h1>
    <h3>Customised Medications for Patients</h3>
    <p>Lorem ipsum dolor sit amet, consectetur adipiscing elit, sed do eiusmod tempor incididunt ut labore et dolore magna aliqua. Ut enim ad minim veniam, quis nostrud exercitation ullamco laboris nisi ut aliquip ex ea commodo consequat.</p>
    <span class="hero-btn">Contact us today</span>
  </div>
</section>

<main class="content">
  <h2>WHAT IS COMPOUNDING PHARMACY?</h2>
  <p class="subtitle">Lorem ipsum dolor sit amet, consectetur adipiscing elit, sed do eiusmod tempor incididunt</p>
  <p class="body">With today's exciting care, the practice of making up medicines has been around since before the first recorded formulas and has long been a trusted part of community pharmacy. Our purpose built preparation laboratory lets our pharmacists prepare each medicine to suit the individual needs of patients, doctors and veterinary clients, adjusting strength, form and flavour where a standard product does not fit. Compounding allows us to remove unwanted ingredients, combine medicines into one dose and provide options for children, older patients and animals alike.</p>
  <div class="services">
    <div class="service">
      <div class="service-icon"><svg viewBox="0 0 56 56"><rect x="8" y="20" width="40" height="16" rx="8" fill="#fff" transform="rotate(-35 28 28)"/></svg></div>
      <h4>CONSECTETUR ADIPISCING</h4>
      <p>Lorem ipsum dolor sit amet consectetur adipiscing elit sed do eiusmod tempor</p>
    </div>
    <div class="service">
      <div class="service-icon green"><svg viewBox="0 0 56 56"><path d="M28 6C20 18 14 26 14 34a14 14 0 0 0 28 0c0-8-6-16-14-28z" fill="#fff"/></svg></div>
      <h4>EIUSMOD TEMPOR</h4>
      <p>Lorem ipsum dolor sit amet consectetur adipiscing elit sed do eiusmod tempor</p>
    </div>
    <div class="service">
      <div class="service-icon"><svg viewBox="0 0 56 56"><rect x="14" y="10" width="28" height="36" rx="3" fill="#fff"/><rect x="20" y="18" width="16" height="3" fill="#1b5fae"/><rect x="20" y="26" width="16" height="3" fill="#1b5fae"/><rect x="20" y="34" width="10" height="3" fill="#1b5fae"/></svg></div>
      <h4>ET DOLORE MAGNA</h4>
      <p>Lorem ipsum dolor sit amet consectetur adipiscing elit sed do eiusmod tempor</p>
    </div>
    <div class="service">
      <div class="service-icon"><svg viewBox="0 0 56 56"><path d="M22 8h12v14h14v12H34v14H22V34H8V22h14z" fill="#fff"/></svg></div>
      <h4>NOSTRUD EXERCITATION</h4>
      <p>Lorem ipsum dolor sit amet consectetur adipiscing elit sed do eiusmod tempor</p>
    </div>
  </div>
  <p class="body">A pharmacist making up a medicine is held to the same high standards as any other dispensing service. Each preparation is checked against the prescriber's instructions and recorded in full, so that patients and their doctors can trust every dose. Our team works closely with local general practitioners, specialists and veterinarians to find the right solution for each person or animal in their care.</p>
  <p class="body" style="margin-top:18px">We invite you to visit our store or contact our friendly pharmacists to discuss how a compounded medicine could help you or your pet today.</p>
  <h2 class="features-title">FEATURE ITEMS</h2>
  <div class="features">
    <div class="feature"><div class="feature-photo" role="img" aria-label="Medical professional reviewing patient information" style="background:linear-gradient(135deg,#cfd8e2,#7d93ab)"></div><h5>Hit Article</h5></div>
    <div class="feature"><div class="feature-photo" role="img" aria-label="Patient receiving a skin therapy treatment" style="background:linear-gradient(135deg,#f1e2d6,#c9a48e)"></div><h5>Scar Therapy</h5></div>
    <div class="feature"><div class="feature-photo" role="img" aria-label="Doctor examining a patient's thyroid" style="background:linear-gradient(135deg,#e9edf1,#a9b8c6)"></div><h5>Thyroid Extract</h5></div>
  </div>
</main>

<footer class="site-footer">
  <div class="footer-col">
    <h4>OPENING HOURS</h4>
    <p>7 DAYS A WEEK 8AM TO 9PM</p>
    <p>8:00 AM TO 8:00 PM</p>
    <p style="margin-top:16px">Visit us during our opening hours to speak with our pharmacists about custom medicines.</p>
  </div>
  <div class="footer-col" style="width:300px">
    <h4>CONTACT MAP</h4>
    <div class="map" role="img" aria-label="Map showing the pharmacy location"></div>
  </div>
  <div class="footer-col" style="width:340px">
    <h4>CONTACT US</h4>
    <div class="fc-item"><svg viewBox="0 0 24 24"><path d="M6.6 10.8a15 15 0 0 0 6.6 6.6l2.2-2.2a1 1 0 0 1 1-.25 11.4 11.4 0 0 0 3.6.6 1 1 0 0 1 1 1V20a1 1 0 0 1-1 1A17 17 0 0 1 3 4a1 1 0 0 1 1-1h3.5a1 1 0 0 1 1 1c0 1.25.2 2.45.6 3.6a1 1 0 0 1-.25 1z"/></svg>08 5550 1234</div>
    <div class="fc-item"><svg viewBox="0 0 24 24"><path d="M6.6 10.8a15 15 0 0 0 6.6 6.6l2.2-2.2a1 1 0 0 1 1-.25 11.4 11.4 0 0 0 3.6.6 1 1 0 0 1 1 1V20a1 1 0 0 1-1 1A17 17 0 0 1 3 4a1 1 0 0 1 1-1h3.5a1 1 0 0 1 1 1c0 1.25.2 2.45.6 3.6a1 1 0 0 1-.25 1z"/></svg>08 5550 1235</div>
    <div class="fc-item"><svg viewBox="0 0 24 24"><path d="M2 5h20v14H2zm2 2v.5l8 5 8-5V7z"/></svg>compounding@westbrookchemist.example</div>
  </div>
</footer>
<div class="copyright">Copyright © 2015 Westbrook Compounding Pharmacy. Privacy policy</div>
</body>
</html>
```